Need help in designing new business card utilizing our new logo.

BuildMark Solutions works with Construction Business Owners, Managers & IT Professionals to strengthen software usage and increase user productivity.

Our Construction Accounting and Mobile Field Management Software Clients engage with us in the following areas:

New Software Implementations
Software Re-Implementations
Redesigning Software Usage at the User Level
Project Coordination & Management
Continued Software Support

Old tag line:
Weighing Options - Implementing Solutions

www.buildmark-solutions.example

Ridge 4 is a product, but not needed for a new business card.

```html
<!DOCTYPE html>
<html lang="en">
<head>
<meta charset="utf-8">
<title>BuildMark Solutions – Business Card</title>
<link rel="stylesheet" href="https://fonts.googleapis.com/css2?family=PT+Sans:wght@400;700&display=swap">
<style>
  :root {
    --brand-blue: #1a16a8;
    --back-blue: #1612a4;
    --soft-grey: #bdbdbd;
    --text-grey: #4a4a4a;
    --band-grey: #d4d4d4;
    --card-white: #ffffff;
    --stage: #2e2e2e;
  }
  * { margin: 0; padding: 0; box-sizing: border-box; }
  html, body { width: 1200px; height: 960px; overflow: hidden; }
  body {
    position: relative;
    background: var(--stage);
    font-family: "PT Sans", "Helvetica Neue", Arial, sans-serif;
  }
  .card {
    position: absolute;
    width: 600px;
    height: 342px;
    overflow: hidden;
  }
  .card-front { left: 322px; top: 110px; background: var(--card-white); }
  .card-back  { left: 320px; top: 493px; background: var(--back-blue); color: #fff; }

  /* Front */
  .brand-mark {
    position: absolute; left: 32px; top: 150px;
    display: flex; align-items: center; gap: 10px;
  }
  .brand-square { width: 22px; height: 22px; background: var(--brand-blue); }
  .brand-name {
    font-size: 23px; font-weight: 700; color: var(--brand-blue);
    letter-spacing: 0.5px; white-space: nowrap;
  }
  .divider {
    position: absolute; left: 283px; top: 75px;
    width: 2px; height: 190px; background: #d8d8d8;
  }
  .contact { position: absolute; left: 307px; top: 80px; color: var(--text-grey); }
  .contact-name {
    font-size: 20px; font-weight: 700; color: var(--brand-blue);
    letter-spacing: 0.2px; line-height: 24px;
  }
  .contact-role {
    font-size: 15px; font-weight: 700; color: var(--soft-grey);
    line-height: 18px; margin-bottom: 14px;
  }
  .contact-address { font-size: 15px; line-height: 19px; margin-bottom: 9px; }
  .contact-list { list-style: none; font-size: 15px; line-height: 19px; }
  .contact-list li { display: flex; align-items: center; gap: 8px; }
  .contact-list svg { width: 14px; height: 14px; fill: var(--brand-blue); flex: none; }

  .footer-strip {
    position: absolute; left: 0; bottom: 0; width: 100%; height: 8px;
    background: var(--band-grey);
  }
  .footer-band {
    position: absolute; left: 64px; bottom: 0; width: 468px; height: 34px;
    background: var(--brand-blue);
    clip-path: polygon(20px 0, 448px 0, 468px 100%, 0 100%);
    color: #fff; font-size: 14.5px; text-align: center; line-height: 34px;
    letter-spacing: 0.2px;
  }

  /* Back */
  .back-brand {
    position: absolute; left: 40px; top: 158px;
    font-size: 25px; font-weight: 700; color: #fff; letter-spacing: 0.5px;
  }
  .services { position: absolute; left: 236px; top: 78px; }
  .services-intro {
    font-size: 15px; font-weight: 700; text-transform: uppercase;
    line-height: 19px; margin-bottom: 1px;
  }
  .services-list { list-style: none; font-size: 15.5px; line-height: 19px; }
  .services-list li::before { content: "• "; }
  .tagline {
    position: absolute; left: 0; top: 296px; width: 556px;
    text-align: center; font-size: 15px; letter-spacing: 0.2px;
  }
</style>
</head>
<body>

<section class="card card-front" aria-label="Business card front">
  <div class="brand-mark">
    <span class="brand-square"></span>
    <span class="brand-name">BuildMark Solutions</span>
  </div>
  <div class="divider"></div>
  <div class="contact">
    <p class="contact-name">DANA R.WHITLOW</p>
    <p class="contact-role">OWNER</p>
    <p class="contact-address">14b harbor street-PMB118<br>millbrook falls NY 10990</p>
    <ul class="contact-list">
      <li><svg viewBox="0 0 16 16" aria-hidden="true"><path d="M1 6c0-2 3-3 7-3s7 1 7 3v1h-3V5.5H4V7H1z M4 8h8l2 6H2z"/></svg>800-555-0142ext.100</li>
      <li><svg viewBox="0 0 16 16" aria-hidden="true"><path d="M4 0h8a1 1 0 0 1 1 1v14a1 1 0 0 1-1 1H4a1 1 0 0 1-1-1V1a1 1 0 0 1 1-1zm1 2v10h6V2z"/></svg>555-301-7724</li>
      <li><svg viewBox="0 0 16 16" aria-hidden="true"><path d="M1 4h14v9H1z" /><path d="M1 4l7 5 7-5" fill="none" stroke="#fff" stroke-width="1.2"/></svg>dana.whitlow@buildmark-solutions.example</li>
      <li><svg viewBox="0 0 16 16" aria-hidden="true"><circle cx="8" cy="8" r="7"/><path d="M1 8h14M8 1c3 3 3 11 0 14M8 1c-3 3-3 11 0 14" fill="none" stroke="#fff" stroke-width="1"/></svg>www.buildmark-solutions.example</li>
    </ul>
  </div>
  <div class="footer-strip"></div>
  <div class="footer-band">CONSTRUCTION ACCOUNTING SOFTWARE CONSULTANTS</div>
</section>

<section class="card card-back" aria-label="Business card back">
  <p class="back-brand">BuildMark</p>
  <div class="services">
    <p class="services-intro">Our construction accounting<br>and mobile field management<br>software clients engage with us<br>in the following areas:</p>
    <ul class="services-list">
      <li>New Software Implementations</li>
      <li>Software Re-Implementations</li>
      <li>Redesigning Software Usage at the User Level</li>
      <li>Project Coordination &amp; Management</li>
      <li>Continued Software Support</li>
    </ul>
  </div>
  <p class="tagline">WEIGHING OPTIONS - IMPLEMENTING SOLUTIONS</p>
</section>

</body>
</html>
```